Lumaris Project 1 - Business Card For Co-Owners

We are an all women's gym located in Seattle, WA. We have been working the past year to elevate our brand and are looking for high quality business card design. I'm including some variations of our logo and have also included an inspiration photo. Our new website is launching on Feb 1 to give you a better idea about who we are (lumaristudio.example). We really love the inspiration business card, some of the key points we like about it:
- the geometric pattern on the back side with gloss texture.
- the rounded corners.
- the simple, clean, strong, yet feminine aesthetic.

Target Market(s)

Women - ages 18-65

Contact Information for Business Card

Company Logo
Company Name
Name
Title
Phone
Email
Website

Font styles to use
Other font styles liked:
• Futura (SEE NOTES)

Colors
e34297

Requirements
Must have
• We really love the inspiration business card, some of the key points we like about it:
• - the geometric pattern on the back side with gloss texture.
• - the dark front side with info.
• - the rounded corners.
• - the simple, clean, strong, yet feminine aesthetic.
• See Logo attached for colors - can be a slight variation of the pink of works better on a dark background
Nice to have
• Futura is one of the fonts used in our logo, but any font that complements the logo will work. I played around a little with design and wasn't wowed by the look of futura, but I'm also not a designer :)
• - the rounded corners.

```html
<!DOCTYPE html>
<html lang="en">
<head>
<meta charset="utf-8">
<title>Lumaris Business Card</title>
<link rel="stylesheet" href="https://fonts.googleapis.com/css2?family=Lato:wght@400;700;900&display=swap">
<style>
  :root {
    --stage: #e8e8e8;
    --card-light: #ffffff;
    --card-dark: #211e20;
    --band-a: #f6f6f6;
    --band-b: #e9e9e9;
    --fine-line: rgba(0, 0, 0, 0.035);
    --ink: #231f20;
    --paper-text: #f4f4f4;
    --muted-light: #bdbdbd;
    --pink: #e34297;
  }
  * { margin: 0; padding: 0; box-sizing: border-box; }
  html, body { width: 1200px; height: 586px; overflow: hidden; }
  body {
    background: var(--stage);
    font-family: "Lato", Arial, sans-serif;
    position: relative;
  }

  .card {
    position: absolute;
    top: 128px;
    width: 500px;
    height: 300px;
    border-radius: 16px;
    overflow: hidden;
  }
  .card--back {
    left: 60px;
    border-top-left-radius: 0;
    border-bottom-left-radius: 0;
    background: var(--card-light);
  }
  .card--front { left: 626px; background: var(--card-dark); }

  /* geometric diagonal bands with a fine gloss line texture */
  .back-pattern {
    position: absolute;
    inset: 0;
    background:
      repeating-linear-gradient(-45deg, var(--fine-line) 0 1px, transparent 1px 4px),
      repeating-linear-gradient(-28deg, var(--band-a) 0 34px, var(--band-b) 34px 40px),
      var(--band-a);
  }
  .back-gloss {
    position: absolute;
    inset: 0;
    background: linear-gradient(135deg, rgba(255,255,255,0.55) 0%, rgba(255,255,255,0) 45%, rgba(255,255,255,0.25) 100%);
  }
  .back-brand {
    position: absolute;
    left: 0; right: 0;
    top: 122px;
    text-align: center;
    font-weight: 900;
    font-size: 42px;
    letter-spacing: 1px;
    line-height: 1;
    color: var(--ink);
  }
  .back-brand__dot {
    display: inline-block;
    width: 12px; height: 12px;
    border-radius: 50%;
    background: var(--pink);
    margin-left: 6px;
    vertical-align: 4px;
  }

  .front-texture {
    position: absolute;
    inset: 0;
    background: repeating-linear-gradient(-45deg, rgba(255,255,255,0.025) 0 1px, transparent 1px 4px);
  }

  .person { position: absolute; left: 40px; top: 80px; }
  .person__name { font-size: 16px; font-weight: 700; color: var(--paper-text); line-height: 1.2; }
  .person__name .surname { color: var(--pink); }
  .person__title { font-size: 10.5px; color: var(--muted-light); margin-top: 5px; }

  .contact { position: absolute; left: 40px; top: 151px; list-style: none; }
  .contact__item {
    display: flex; align-items: center; gap: 8px;
    font-size: 12px; color: var(--paper-text);
    height: 18px; margin-bottom: 6px;
  }
  .contact__icon { width: 17px; height: 17px; flex: none; }

  .address {
    position: absolute; left: 42px; top: 228px;
    font-style: normal; font-weight: 700; font-size: 11.5px;
    line-height: 19px; color: var(--pink);
  }

  .front-brand {
    position: absolute; left: 276px; top: 146px;
    width: 204px; text-align: center;
    font-weight: 900; font-size: 40px; line-height: 1;
    letter-spacing: 1px; color: var(--paper-text);
  }
</style>
</head>
<body>
  <section class="card card--back">
    <div class="back-pattern" role="img" aria-label="Geometric diagonal band pattern with gloss texture"></div>
    <div class="back-gloss"></div>
    <div class="back-brand">Lumaris<span class="back-brand__dot"></span></div>
  </section>

  <section class="card card--front">
    <div class="front-texture"></div>
    <div class="person">
      <div class="person__name">Dana <span class="surname">Whitfield</span></div>
      <div class="person__title">Director &amp; Founder</div>
    </div>

    <ul class="contact">
      <li class="contact__item">
        <svg class="contact__icon" viewBox="0 0 20 20" aria-hidden="true">
          <circle cx="10" cy="10" r="10" fill="var(--pink)"/>
          <path d="M5.5 8.5c0-1.5 2-2.5 4.5-2.5s4.5 1 4.5 2.5v.8h-2.2v-1h-4.6v1H5.5z M7 10h6l1.3 3.8H5.7z" fill="#fff"/>
        </svg>
        555-014-2290
      </li>
      <li class="contact__item">
        <svg class="contact__icon" viewBox="0 0 20 20" aria-hidden="true">
          <circle cx="10" cy="10" r="10" fill="var(--pink)"/>
          <rect x="5" y="6.5" width="10" height="7" fill="#fff"/>
          <path d="M5 6.5l5 4 5-4" fill="none" stroke="var(--pink)" stroke-width="1"/>
        </svg>
        dana@lumaristudio.example
      </li>
      <li class="contact__item">
        <svg class="contact__icon" viewBox="0 0 20 20" aria-hidden="true">
          <circle cx="10" cy="10" r="10" fill="var(--pink)"/>
          <circle cx="10" cy="10" r="5" fill="none" stroke="#fff" stroke-width="1.2"/>
          <ellipse cx="10" cy="10" rx="2.2" ry="5" fill="none" stroke="#fff" stroke-width="1"/>
          <path d="M5 10h10" stroke="#fff" stroke-width="1"/>
        </svg>
        lumaristudio.example
      </li>
    </ul>

    <address class="address">
      2150 Harbor Lane<br>
      Meadow Park, Ohio 44012
    </address>

    <div class="front-brand">Lumaris</div>
  </section>
</body>
</html>
```